Merry Perch Wild Bird Food Gusset Bag Deisgn

We’re looking to transition from our current packaging—using a sticker on a bag—to a fully printed film design. The goal is to modernize the look and make it more fun while staying true to our existing brand identity.
We’d like to retain the same color scheme, fonts, and artwork style currently used on our bags. The barcode and product information should be placed on the back of the bag.
Bag specifications:
Dimensions: 410mm (length) x 530mm (width)
Design: Predominantly white with strategically placed transparent areas to allow the product to be seen inside.
There are 10 different bag designs required for this range.
We have attached our current labels of each product there is a Circle one and also a rectangle one that all all product information
We would also likes explained and also a image showing the these 5L bags refill 5L Tubs
We’ll also attach some example bags that represent the look and feel we’re aiming for in the new designs.
The bag is a gusset bag, Icon attached as an example
Target Market(s)
Wild Bird Food Buyers
Look and feel

```html
<!DOCTYPE html>
<html lang="en">
<head>
<meta charset="utf-8">
<title>Merry Perch Black Sunflower Bag</title>
<link href="https://fonts.googleapis.com/css2?family=Chewy&family=Oswald:wght@300;400;500&display=swap" rel="stylesheet">
<style>
:root{
  --stage:#8a8a8a;
  --film:#efeee6;
  --gusset:#5fb52e;
  --gusset-light:#a6dd7c;
  --ink:#2b2b2b;
  --teal:#2a9a92;
  --teal-soft:#7cc7c1;
  --red:#e0413c;
  --green-ring:#96c95b;
  --seed-dark:#2c2f33;
  --seed-mid:#5a5f66;
}
*{box-sizing:border-box;margin:0;padding:0}
html,body{width:1200px;height:960px;overflow:hidden}
body{background:var(--stage);font-family:"Oswald",sans-serif;color:var(--ink);position:relative}
.bag{position:absolute;top:70px;height:820px;background:var(--film);display:flex;box-shadow:0 10px 30px rgba(0,0,0,.25)}
.gusset{width:50px;background:linear-gradient(90deg,var(--gusset),var(--gusset-light) 60%,var(--gusset))}
.seal{position:absolute;left:0;right:0;top:0;height:22px;background:repeating-linear-gradient(180deg,#e2e1d9 0 2px,var(--film) 2px 5px)}
.front{left:90px;width:480px}
.back{left:630px;width:480px}
.face{flex:1;position:relative;display:flex;flex-direction:column;align-items:center}
.brand{display:flex;align-items:center;gap:6px;color:var(--teal);font-weight:500;font-size:20px;line-height:1}
.brand-dot{width:12px;height:12px;border-radius:50%;background:var(--teal)}
.front .brand{margin-top:100px}
.title{font-family:"Chewy",cursive;text-align:center;color:var(--ink);line-height:.95}
.front .title{font-size:64px;margin-top:26px}
.front .art{width:220px;height:220px;margin-top:14px;border-radius:40% 40% 20% 20%;background:radial-gradient(circle at 60% 40%,#f3c43a 0 18%,#7cbf57 40%,#8f9cb0 70%,transparent 72%)}
.window{position:absolute;left:12px;right:12px;top:555px;height:190px;background:linear-gradient(160deg,var(--seed-mid),var(--seed-dark));border-radius:30% 30% 0 0/12% 12% 0 0}
.weight{position:absolute;right:22px;top:700px;font-family:"Chewy",cursive;font-size:32px;color:#111}
.grass{position:absolute;left:0;right:0;bottom:0;height:75px;background:linear-gradient(180deg,rgba(120,200,80,0),#6fc043 60%,#4f9e2b)}
.back .face{flex-direction:row;align-items:stretch}
.col{display:flex;flex-direction:column;align-items:center;padding:0 14px}
.col-story{width:250px;border-right:1px solid #dcdbd2}
.col-info{flex:1;padding-top:100px}
.back .art{width:120px;height:90px;margin-top:90px;border-radius:40%;background:radial-gradient(circle at 60% 45%,#f3c43a 0 18%,#7cbf57 45%,#8f9cb0 70%,transparent 72%)}
.headline{font-family:"Chewy",cursive;font-size:17px;text-align:center;line-height:1.55;margin-top:26px}
.copy{font-weight:300;font-size:12.5px;line-height:1.65;text-align:justify;margin-top:6px}
.sub{font-family:"Chewy",cursive;font-size:16px;margin-top:10px}
.label{align-self:flex-start;font-weight:500;font-size:14px;margin-top:12px}
.detail{align-self:flex-start;font-weight:300;font-size:13px;line-height:1.5}
.back .brand{font-size:13px}
.back .title{font-size:30px;margin-top:12px}
.icon{margin-top:20px}
.icon-text{font-weight:500;font-size:13px;text-align:center;line-height:1.15;margin-top:4px}
.comp{color:var(--teal-soft);font-weight:500;font-size:14px;margin-top:22px}
.info{font-size:13px;text-align:center;line-height:1.5}
.spec{margin-top:26px;font-weight:500}
.blank{margin-top:28px;font-weight:300}
.disposal{display:flex;gap:14px;margin-top:auto;margin-bottom:60px}
</style>
</head>
<body>

<section class="bag front">
  <div class="seal"></div>
  <div class="gusset"></div>
  <div class="face">
    <div class="brand"><span class="brand-dot"></span>Merry Perch</div>
    <h1 class="title">Black<br>Sunflower</h1>
    <div class="art" role="img" aria-label="Illustration of a garden bird perched on stones beside sunflowers and grasses, with black seeds scattered below"></div>
    <div class="window" role="img" aria-label="Clear window showing black sunflower seeds inside the bag"></div>
    <div class="weight">5lbs</div>
    <div class="grass" role="img" aria-label="Illustrated green grass along the base of the bag"></div>
  </div>
</section>

<section class="bag back">
  <div class="seal"></div>
  <div class="gusset"></div>
  <div class="face">
    <div class="col col-story">
      <div class="art" role="img" aria-label="Small illustration of a garden bird with sunflowers and seeds"></div>
      <h2 class="headline">Attract a Variety of Birds<br>With Nutritious Black<br>Sunflower Seeds!</h2>
      <p class="copy">Turn your garden into a lively bird sanctuary with our Black Sunflower 5L Bag, the perfect choice for bird enthusiasts who want to provide their avian visitors with a nutritious and high-energy treat. Known for their high oil content and appeal to a wide range of bird species, these premium black sunflower seeds are sure to make your garden a favorite feeding spot.</p>
      <h3 class="sub">Easy to Use:</h3>
      <p class="copy">Fill your bird feeders, place on bird tables, or scatter on the ground to create an inviting space for birds. Watch as they flock to your garden, bringing vibrant colors and cheerful song to your outdoor area.</p>
      <p class="label">Address:</p>
      <p class="detail">Fenwick Imports, Oakridge Mill<br>Business Park, Ashbury, AB12 3CD</p>
      <p class="label">Contact:</p>
      <p class="detail">Sales@fenwickimports.co.uk</p>
    </div>
    <div class="col col-info">
      <div class="brand"><span class="brand-dot"></span>Merry Perch</div>
      <h2 class="title">Black<br>Sunflower</h2>
      <svg class="icon" width="62" height="62" viewBox="0 0 62 62" aria-hidden="true">
        <circle cx="31" cy="31" r="27" fill="none" stroke="var(--red)" stroke-width="6"/>
        <line x1="12" y1="50" x2="50" y2="12" stroke="var(--red)" stroke-width="6"/>
      </svg>
      <p class="icon-text">Not for human<br>consumption</p>
      <svg class="icon" width="62" height="62" viewBox="0 0 62 62" aria-hidden="true">
        <circle cx="31" cy="31" r="27" fill="none" stroke="var(--green-ring)" stroke-width="5"/>
        <rect x="22" y="14" width="18" height="34" rx="9" fill="var(--teal-soft)" stroke="var(--teal)" stroke-width="2" transform="rotate(-35 31 31)"/>
      </svg>
      <p class="icon-text">May Contain<br>Nuts</p>
      <p class="comp">Composition:</p>
      <p class="info">Black Sunflower</p>
      <p class="info spec">Net Weight: 2000g<br>SKU: MP30</p>
      <p class="info blank">Expiry Date:</p>
      <p class="info blank">Batch:</p>
      <div class="disposal" aria-hidden="true">
        <svg width="30" height="30" viewBox="0 0 30 30"><circle cx="15" cy="15" r="13" fill="none" stroke="#222" stroke-width="2"/><path d="M10 18 L15 9 L20 18 Z" fill="none" stroke="#222" stroke-width="2"/></svg>
        <svg width="30" height="30" viewBox="0 0 30 30"><circle cx="15" cy="15" r="13" fill="none" stroke="#222" stroke-width="2"/><rect x="11" y="11" width="8" height="10" fill="none" stroke="#222" stroke-width="2"/><line x1="9" y1="10" x2="21" y2="10" stroke="#222" stroke-width="2"/></svg>
      </div>
    </div>
  </div>
</section>

</body>
</html>
```